Business Card Design - Photographer

I am a landscape photographer and I require a business card design. 

I require two designs:
1)  a double sided business card
 and
b)  a single sided business card 

The single sided design can either be the same as the double sided (with just one side having all the information)....or it can be an entire new design. Its up to you.

My corporate colours are (CMYK):

Blue   69, 32, 0, 0
Grey  72,  64,  47,  31
Green  32,  2,  91,  0
Yellow   0, 19, 92, 0
Orange  0, 39, 75, 0

Colour space in final file should be in CMYK.

The details that need to be included on the card:

- Use the provided Logo
- Name: Wiktor Baranowski
- Email:   sales@vistalumeworks.com.au
- Website:    vistalumeworks.com.au
- Twitter:    twitter.com/vistalumeworks
- Facebook:   facebook.com/vistalumeworks
- Mobile  0417 539 662

Please use the attached template to design the logo to the specified size, including the marked bleed lines. I have also attached my logo in PNG (transparent background) and ai format for you to use.

The final file should be:
- Photoshop version with layers so I can edit the name/text etc. All non vector files should be high resolution at 1039 x 697 pixels at 300 dpi.

I also require a file as:
- Vector based PDF

Anyway questions please contact me.

Thank you

Industry/Entity Type

Landscape

Logo styles of interest
Pictorial/Combination Logo
Abstract Logo
Wordmark Logo
Lettermark Logo
Requirements
Must have
• The details that need to be included on the card:

- Use the provided Logo
- Name: Wiktor Baranowski
- Email: sales@vistalumeworks.com.au
- Website: vistalumeworks.com.au
- Twitter: twitter.com/vistalumeworks
- Facebook: facebook.com/vistalumeworks
- Mobile 0417 539 662

```html
<!DOCTYPE html>
<html lang="en">
<head>
<meta charset="utf-8">
<title>Vistalume Works – Business Cards</title>
<link href="https://fonts.googleapis.com/css2?family=Cinzel:wght@400;600&display=swap" rel="stylesheet">
<style>
  :root {
    --backdrop: #86878b;
    --card-white: #ffffff;
    --panel-slate: #3d4051;
    --accent-yellow: #fdc800;
    --ink-slate: #3d4051;
    --text-light: #ffffff;
    --mark-faint: rgba(255,255,255,0.05);
  }
  html, body {
    margin: 0;
    padding: 0;
    width: 976px;
    height: 1200px;
    overflow: hidden;
    background: var(--backdrop);
  }
  .sheet {
    position: relative;
    width: 976px;
    height: 1200px;
  }
  .card {
    position: absolute;
    left: 78px;
    width: 817px;
    height: 466px;
    border-radius: 38px;
    overflow: hidden;
    background: var(--card-white);
    box-shadow: 6px 8px 14px rgba(0,0,0,0.35);
    font-family: "Cinzel", "Times New Roman", serif;
  }
  .card--front { top: 77px; }
  .card--back { top: 667px; }
  .card__art {
    position: absolute;
    inset: 0;
    width: 817px;
    height: 466px;
  }
  .brand {
    position: absolute;
    left: 18px;
    top: 108px;
    width: 380px;
    text-align: center;
  }
  .brand__dot {
    display: block;
    width: 128px;
    height: 128px;
    margin: 0 auto 20px;
    border-radius: 50%;
    background: var(--ink-slate);
  }
  .brand__name {
    margin: 0;
    font-size: 34px;
    font-weight: 600;
    letter-spacing: 1px;
    color: var(--ink-slate);
    white-space: nowrap;
  }
  .website {
    position: absolute;
    left: 470px;
    width: 330px;
    top: 238px;
    text-align: center;
    color: var(--text-light);
    font-size: 15px;
    letter-spacing: 0.5px;
    margin: 0;
  }
  .website strong { font-size: 19px; font-weight: 600; }
  .contact {
    position: absolute;
    left: 470px;
    width: 335px;
    top: 180px;
    margin: 0;
    padding: 0;
    list-style: none;
    text-align: center;
    color: var(--text-light);
    font-size: 16px;
    letter-spacing: 0.5px;
  }
  .contact li { height: 36.5px; line-height: 26px; white-space: nowrap; }
</style>
</head>
<body>
<main class="sheet">

  <section class="card card--front">
    <svg class="card__art" viewBox="0 0 817 466" aria-hidden="true">
      <path d="M497 0 Q300 233 522 466 L817 466 L817 0 Z" fill="var(--accent-yellow)"/>
      <path d="M518 0 Q326 233 528 466 L817 466 L817 0 Z" fill="var(--card-white)"/>
      <path d="M532 0 Q353 233 530 466 L817 466 L817 0 Z" fill="var(--panel-slate)"/>
      <circle cx="651" cy="240" r="142" fill="var(--mark-faint)"/>
    </svg>
    <div class="brand">
      <span class="brand__dot"></span>
      <p class="brand__name">VISTALUME WORKS</p>
    </div>
    <p class="website">www.<strong>VISTALUMEWORKS</strong>.com.au</p>
  </section>

  <section class="card card--back">
    <svg class="card__art" viewBox="0 0 817 466" aria-hidden="true">
      <path d="M497 0 Q300 233 522 466 L817 466 L817 0 Z" fill="var(--accent-yellow)"/>
      <path d="M518 0 Q326 233 528 466 L817 466 L817 0 Z" fill="var(--card-white)"/>
      <path d="M532 0 Q353 233 530 466 L817 466 L817 0 Z" fill="var(--panel-slate)"/>
      <circle cx="651" cy="240" r="142" fill="var(--mark-faint)"/>
    </svg>
    <div class="brand">
      <span class="brand__dot"></span>
      <p class="brand__name">VISTALUME WORKS</p>
    </div>
    <ul class="contact">
      <li>E : sales@vistalumeworks.com.au</li>
      <li>T : twitter.com/vistalumeworks</li>
      <li>F : facebook.com/vistalumeworks</li>
      <li>M : 0417 539 662</li>
    </ul>
  </section>

</main>
</body>
</html>
```